Elegant Business Card for Technology Company

Client is a supplier of innovative industrial communications and automation equipment since 2002. This contest is to gather fresh ideas for a redesign of the existing business card. Client is looking for design that best communicates tagline "Industrial Networking and Computing Specialist".

Design submissions should look modern, clean, elegant and professional. It should not be cluttered. Use white as the primary colour. Orange and black as secondary colour. Refer to jpeg File 1 on the current design.

Fonts used by Client used include Arial Regular, Arial Black, Roboto Regular, Roboto Black and Lato.

The winning design will be sent for offset printing using super white 250gsm artcard paper (open for suggestions).

Target Market(s)

System Engineers, Project Managers, Purchasing Managers from companies providing engineering services for Smart Cities.

Industry/Entity Type

Information Technology

Contact Information for Business Card

Refer to PDF File 3 for Business Card Details. Priority of short contact information would be as follows Name > Job Title > Email > Mobile > Web > Tel > Fax > Business Address >UEN (UEN represents company registration number)

Font styles to use
Sans Serif

Colors
ffffff
f37122
000000
5c5c5c

Requirements
Must have
• Refer to AI File 2 (Company Logo) & PDF File 3 (Information on Namecard)
Should not have
• No QR codes
• No Social Media Icons
• Do not create full Black or Orange colour background

```html
<!DOCTYPE html>
<html lang="en">
<head>
<meta charset="utf-8">
<title>Veltrix Business Card</title>
<link href="https://fonts.googleapis.com/css2?family=Source+Sans+3:wght@400;600;700;800&display=swap" rel="stylesheet">
<style>
  :root {
    --orange: #f37122;
    --white: #ffffff;
    --black: #000000;
    --ink: #2b2b2b;
    --grey: #5c5c5c;
    --stage-top: #2a2a2a;
    --stage-bottom: #050505;
  }
  * { margin: 0; padding: 0; box-sizing: border-box; }
  html, body { width: 1200px; height: 900px; overflow: hidden; }
  body {
    position: relative;
    background: linear-gradient(180deg, var(--stage-top) 0%, #141414 55%, var(--stage-bottom) 100%);
    font-family: "Source Sans 3", Arial, sans-serif;
  }
  .card {
    position: absolute;
    top: 306px;
    width: 440px;
    height: 271px;
    border-radius: 12px;
  }
  .card-front { left: 149px; background: var(--white); }
  .card-back { left: 608px; background: var(--orange); color: var(--white); }

  /* brand mark: circle + name */
  .brand { position: absolute; display: flex; align-items: center; gap: 8px; }
  .brand-dot { width: 52px; height: 52px; border-radius: 50%; flex: none; }
  .brand-name { font-weight: 800; font-size: 38px; letter-spacing: 0.5px; line-height: 1; }
  .card-front .brand { left: 22px; top: 114px; }
  .card-front .brand-dot { background: var(--orange); }
  .card-front .brand-name { color: var(--black); font-size: 34px; }
  .card-back .brand { left: 0; right: 0; top: 44px; justify-content: center; }
  .card-back .brand-dot { background: var(--white); width: 60px; height: 60px; }
  .card-back .brand-name { color: var(--white); font-size: 42px; }

  /* contact block */
  .contact { position: absolute; left: 222px; top: 40px; color: var(--ink); }
  .person-name { color: var(--orange); font-weight: 600; font-size: 17px; line-height: 19px; }
  .person-title { font-size: 12.5px; line-height: 14px; }
  .reg-number { margin-top: 7px; font-size: 12.5px; line-height: 14px; }
  .reg-number .label { color: var(--orange); font-weight: 600; margin-right: 3px; }
  .address { margin-top: 8px; font-size: 12.5px; line-height: 18px; }
  .contact-list { list-style: none; margin-top: 6px; }
  .contact-list li { display: flex; align-items: center; gap: 7px; font-size: 12.5px; height: 18.3px; }
  .contact-list svg { width: 9px; height: 9px; fill: var(--orange); flex: none; margin-left: 3px; }

  /* services */
  .services { position: absolute; left: 0; right: 0; top: 138px; text-align: center; list-style: none; }
  .services li { font-weight: 600; font-size: 13px; line-height: 23.3px; }
  .tagline { position: absolute; left: 0; right: 0; top: 233px; text-align: center; font-weight: 600; font-size: 14.5px; }
</style>
</head>
<body>
  <section class="card card-front" aria-label="Business card front">
    <div class="brand">
      <span class="brand-dot"></span>
      <span class="brand-name">VELTRIX</span>
    </div>
    <div class="contact">
      <p class="person-name">Daniel Koh</p>
      <p class="person-title">Sales Manager</p>
      <p class="reg-number"><span class="label">UEN No:</span>201105577K</p>
      <p class="address">24 Kallen Avenue Norvale Techpark<br>#05-12 &nbsp;(Lobby B), Singapore 418230</p>
      <ul class="contact-list">
        <li><svg viewBox="0 0 10 10" aria-hidden="true"><path d="M2.5 0h5a1 1 0 0 1 1 1v8a1 1 0 0 1-1 1h-5a1 1 0 0 1-1-1V1a1 1 0 0 1 1-1zm0.5 1.5v6h4v-6zM5 8.2a.5.5 0 1 0 0 1 .5.5 0 0 0 0-1z"/></svg>+65 8123 4567</li>
        <li><svg viewBox="0 0 10 10" aria-hidden="true"><path d="M2 0.5l1.6 2-1 1.2c.7 1.4 1.7 2.4 3.1 3.1l1.2-1 2 1.6-.9 1.9C4.5 9 1 5.5.4 1.4z"/></svg>65 6123 4500</li>
        <li><svg viewBox="0 0 10 10" aria-hidden="true"><path d="M2.5 0h4v3h-4zM0.5 3.5h9v5h-2V10h-5V8.5h-2zm2.5 3v2.5h4V6.5z"/></svg>+ 65 6123 4599</li>
        <li><svg viewBox="0 0 10 10" aria-hidden="true"><path d="M0 2h10v6H0zm.8.8L5 5.6l4.2-2.8v-.1H.8z"/></svg>sales@veltrix.example</li>
        <li><svg viewBox="0 0 10 10" aria-hidden="true"><path d="M5 0a5 5 0 1 0 0 10A5 5 0 0 0 5 0zm0 1c.7 0 1.4 1.5 1.5 3.5h-3C3.6 2.5 4.3 1 5 1zM3.5 5.5h3C6.4 7.5 5.7 9 5 9s-1.4-1.5-1.5-3.5z"/></svg>www.veltrix.example</li>
      </ul>
    </div>
  </section>

  <section class="card card-back" aria-label="Business card back">
    <div class="brand">
      <span class="brand-dot"></span>
      <span class="brand-name">VELTRIX</span>
    </div>
    <ul class="services">
      <li>Industrial Enthernet / Wireless / Cellular</li>
      <li>Industrial and Embedded Computing</li>
      <li>Serial / Fieldbus Connectivity</li>
      <li>IP Video Surveilance / Remote Automation</li>
    </ul>
    <p class="tagline">Industrial Networking And Computing Specialist</p>
  </section>
</body>
</html>
```